Fashion Label Startup Business Card Design

Miriam Kettle is a startup fashion designer based on the Gold Coast in QLD Australia. Miriams label " Verona by Kettle " is based upon taking old world design techniques and infusing them modern twist. The card design should incorporate an old world theme using colours like mustard, ocha, black, white and elements of lace pattern.

Card Details:

Miriam Kettle
Fashion Designer
P: 04 0261 5847
E: veronabykettle@mailbrook.example
W: www.socialpage.example/VEronaByKettle

```html
<!DOCTYPE html>
<html lang="en">
<head>
<meta charset="utf-8">
<title>Verona by Kettle – Business Card</title>
<link rel="stylesheet" href="https://fonts.googleapis.com/css2?family=Tinos:wght@400;700&display=swap">
<style>
  :root {
    --backdrop: #232323;
    --mustard: #ffdf5e;
    --mustard-deep: #efcd4c;
    --mustard-groove: #d9b942;
    --leaf-green: #4f8739;
    --ink-green: #4a7a32;
    --label-black: #0e0e0a;
    --ornament-dark: #2a2614;
    --ornament-gold: #8c7a2c;
  }
  * { margin: 0; padding: 0; box-sizing: border-box; }
  html, body {
    width: 1200px; height: 1000px; overflow: hidden;
    background: var(--backdrop);
    font-family: "Tinos", "Times New Roman", serif;
  }
  .canvas { position: relative; width: 1200px; height: 1000px; }

  .card {
    position: absolute;
    width: 620px; height: 372px;
    background: var(--mustard);
    border-radius: 22px;
    overflow: hidden;
    box-shadow: 0 10px 26px rgba(0,0,0,.45);
  }
  .card--front { left: 530px; top: 70px; }
  .card--back { left: 60px; top: 540px; }

  /* Front */
  .front__band {
    position: absolute; left: 0; right: 0; top: 166px; height: 40px;
    background: var(--leaf-green);
  }
  .front__ornament {
    position: absolute; left: 100px; top: 66px; width: 420px; height: 240px;
  }
  .front__label {
    position: absolute; left: 180px; top: 141px; width: 260px; height: 90px;
    background: var(--label-black);
    border: 2px solid var(--mustard);
    outline: 3px solid var(--label-black);
    display: flex; align-items: center; justify-content: center;
  }
  .brand-name {
    color: var(--mustard);
    font-weight: 400;
    font-size: 34px;
    white-space: nowrap;
  }

  /* Back */
  .back__watermark {
    position: absolute; left: 0; right: 0; top: 62px;
    text-align: center;
    font-size: 64px; font-weight: 400;
    color: var(--mustard-deep);
    white-space: nowrap;
  }
  .back__groove {
    position: absolute; left: 0; right: 0; height: 2px;
    background: var(--mustard-groove);
    box-shadow: 0 3px 6px rgba(150,120,20,.35);
  }
  .back__groove--upper { top: 150px; }
  .back__groove--lower { top: 234px; }
  .back__details {
    position: absolute; left: 0; right: 0;
    text-align: center; color: var(--ink-green);
  }
  .holder { top: 180px; }
  .holder__name { font-size: 22px; font-weight: 700; line-height: 24px; }
  .holder__title { font-size: 17px; line-height: 22px; }
  .contact { top: 258px; font-size: 16px; line-height: 31px; }
</style>
</head>
<body>
<main class="canvas">

  <section class="card card--front" aria-label="Business card front">
    <div class="front__band"></div>
    <svg class="front__ornament" viewBox="0 0 420 240" role="img" aria-label="Ornate old-world scrollwork frame surrounding the label name">
      <defs>
        <radialGradient id="ornamentTone" cx="50%" cy="50%" r="60%">
          <stop offset="0%" stop-color="var(--ornament-gold)"/>
          <stop offset="100%" stop-color="var(--ornament-dark)"/>
        </radialGradient>
      </defs>
      <rect x="4" y="4" width="412" height="232" rx="110" ry="110" fill="url(#ornamentTone)"/>
    </svg>
    <div class="front__label">
      <span class="brand-name">Verona by Kettle</span>
    </div>
  </section>

  <section class="card card--back" aria-label="Business card back">
    <div class="back__watermark" aria-hidden="true">Verona by Kettle</div>
    <div class="back__groove back__groove--upper"></div>
    <div class="back__details holder">
      <p class="holder__name">Miriam Kettle</p>
      <p class="holder__title">Fashion Designer</p>
    </div>
    <div class="back__groove back__groove--lower"></div>
    <div class="back__details contact">
      <p class="contact__phone">04 0261 5847</p>
      <p class="contact__email">veronabykettle@mailbrook.example</p>
      <p class="contact__web">www.socialpage.example/VEronaByKettle</p>
    </div>
  </section>

</main>
</body>
</html>
```